Velvet Pressings Techno Label Business Card

I'm looking for a very clean business card for my Velvet Pressings music label. The label focusses on techno music. The card should include:

• my name : Tomas Brandt as "Founder & CEO"
• email address: tomas@velvet-pressings.example
• web: www.velvet-pressings.example
• facebook logo + /velvetpress
• twitter logo + /velvetpress
• soundcloud logo + /velvetpressings

Feel free to include your ideas! I'm looking forward to discuss about it.

Tomas

Industry/Entity Type

Business

Contact Information for Business Card

I don't like glossy cards. Prefer matt.

Requirements
Nice to have
• Maybe on one side the complete logo, other side just the icon.
Should not have
• Flashy stuff. Must be clean and business like style.

```html
<!DOCTYPE html>
<html lang="en">
<head>
<meta charset="utf-8">
<title>Velvet Pressings – Business Card</title>
<link href="https://fonts.googleapis.com/css2?family=Open+Sans:wght@400&family=Ubuntu:wght@400;700&display=swap" rel="stylesheet">
<style>
  :root {
    --page-bg: #f0f0f0;
    --brand-orange: #e57017;
    --card-black: #0b0b0b;
    --ink: #111111;
    --muted: #9a9a9a;
    --note-red: #d7254b;
    --note-ink: #222222;
  }
  * { margin: 0; padding: 0; box-sizing: border-box; }
  html, body { width: 1200px; height: 1066px; overflow: hidden; }
  body { background: var(--page-bg); position: relative; font-family: "Open Sans", Arial, sans-serif; }

  .card {
    position: absolute;
    width: 650px;
    height: 392px;
    box-shadow: -18px 22px 40px rgba(0,0,0,0.22);
  }
  .card-front { left: 125px; top: 111px; background: var(--brand-orange); }
  .card-back { left: 388px; top: 561px; background: var(--card-black); }

  /* Front: label name */
  .wordmark {
    position: absolute;
    left: 66px;
    top: 170px;
    display: flex;
    align-items: center;
    gap: 18px;
  }
  .wordmark-square {
    width: 22px; height: 22px;
    background: var(--ink);
    flex: none;
  }
  .wordmark-name {
    font-family: "Ubuntu", Arial, sans-serif;
    font-weight: 700;
    font-size: 46px;
    line-height: 1;
    letter-spacing: -0.5px;
    color: var(--ink);
  }

  /* Back: label name block */
  .back-name {
    position: absolute;
    left: 60px; top: 150px;
    width: 200px;
    font-family: "Ubuntu", Arial, sans-serif;
    font-weight: 700;
    font-size: 34px;
    line-height: 1.1;
    color: var(--brand-orange);
    text-align: center;
  }

  .person { position: absolute; left: 326px; top: 74px; }
  .person-name {
    font-family: "Ubuntu", Arial, sans-serif;
    font-weight: 700;
    font-size: 22px;
    line-height: 1.1;
    color: var(--brand-orange);
    letter-spacing: 0.3px;
  }
  .person-role {
    font-family: "Ubuntu", Arial, sans-serif;
    font-size: 13px;
    color: var(--muted);
    margin-top: 3px;
    letter-spacing: 0.4px;
  }

  .contacts { position: absolute; left: 326px; top: 184px; list-style: none; }
  .contacts li {
    display: flex; align-items: center;
    height: 22.5px;
    font-size: 15px;
    color: var(--muted);
    white-space: nowrap;
  }
  .contact-icon { width: 11px; height: 11px; margin-right: 11px; flex: none; }
  .social-square { width: 10px; height: 10px; background: var(--brand-orange); border-radius: 2px; margin: 0 12px 0 1px; flex: none; }

  /* Colour note */
  .swatch-note { position: absolute; left: 915px; top: 158px; font-family: Arial, sans-serif; }
  .swatch-title { font-size: 24px; color: var(--note-red); margin-bottom: 46px; }
  .swatch-values { list-style: none; font-size: 25px; color: var(--note-ink); line-height: 30.5px; }
</style>
</head>
<body>

  <section class="card card-front" aria-label="Card front">
    <div class="wordmark">
      <span class="wordmark-square"></span>
      <span class="wordmark-name">Velvet Pressings</span>
    </div>
  </section>

  <section class="card card-back" aria-label="Card back">
    <div class="back-name">Velvet<br>Pressings</div>

    <div class="person">
      <div class="person-name">Tomas Brandt</div>
      <div class="person-role">Founder &amp; CEO</div>
    </div>

    <ul class="contacts">
      <li>
        <svg class="contact-icon" viewBox="0 0 12 12" aria-hidden="true"><path d="M2.5 1 L4.5 1 L5.2 3.6 L3.9 4.6 Q5 7 7.4 8.1 L8.4 6.8 L11 7.5 L11 9.5 Q10.5 11 8.8 11 Q2 10 1 3.2 Q1 1.5 2.5 1 Z" fill="var(--brand-orange)"/></svg>
        +31600482915
      </li>
      <li>
        <svg class="contact-icon" viewBox="0 0 12 12" aria-hidden="true"><rect x="0.5" y="2.5" width="11" height="7" fill="var(--brand-orange)"/><path d="M0.8 3 L6 7 L11.2 3" stroke="var(--card-black)" stroke-width="1.1" fill="none"/></svg>
        tomas@velvet-pressings.example
      </li>
      <li>
        <svg class="contact-icon" viewBox="0 0 12 12" aria-hidden="true"><circle cx="6" cy="6" r="5" fill="var(--brand-orange)"/><path d="M1 6 H11 M6 1 V11 M6 1 Q3 6 6 11 M6 1 Q9 6 6 11" stroke="var(--card-black)" stroke-width="0.8" fill="none"/></svg>
        www.velvet-pressings.example
      </li>
      <li><span class="social-square"></span>/velvetpress</li>
      <li><span class="social-square"></span>/velvetpress</li>
      <li><span class="social-square"></span>/velvetpressings</li>
    </ul>
  </section>

  <aside class="swatch-note">
    <div class="swatch-title">Oragne</div>
    <ul class="swatch-values">
      <li>C:0</li>
      <li>M:65</li>
      <li>Y:100</li>
      <li>K:0</li>
    </ul>
  </aside>

</body>
</html>
```